Brenlow Estates Website and Logo Design

We need a new logo and website designed for 'Brenlow Estates Ltd', which is a well established Guernsey property holding company founded in 1934.

The company does not currently have a website. The new website should be similar in style and layout to https://www.quorvanhall.example/.

Target Market(s)

Industry, Media, Tenants

Industry/Entity Type

Property Management

Logo Text

BEL OR Brenlow Estates Ltd OR BE

Coding

Coded - Design and coding required

Number of Pages Required

4 page

Font styles to use
Other font styles liked:
• Helvetica

Requirements
Must have
• The logo laying over the picture (like https://www.quorvanhall.example/).
• Big pictures on homepage (like https://www.quorvanhall.example/)

```html
<!DOCTYPE html>
<html lang="en">
<head>
<meta charset="utf-8">
<title>Brenlow Estates Ltd</title>
<link href="https://fonts.googleapis.com/css2?family=Cinzel:wght@400;700&family=Open+Sans:wght@400;600;700&family=Roboto+Slab:wght@400;700&display=swap" rel="stylesheet">
<style>
:root{
  --blue:#0f86d8;
  --blue-deep:#0a6db6;
  --blue-light:#2aa2ea;
  --navy:#123a5c;
  --ink:#333a42;
  --muted:#6b7580;
  --white:#ffffff;
}
*{margin:0;padding:0;box-sizing:border-box}
html,body{width:1200px;height:3564px;overflow:hidden}
body{font-family:"Open Sans",Helvetica,Arial,sans-serif;color:var(--ink);background:var(--white);font-size:14px}
a{color:inherit;text-decoration:none}

.topbar{height:30px;display:flex;align-items:center;justify-content:space-between;padding:0 70px;font-size:11px;color:var(--muted);border-bottom:1px solid #e5e9ee}
.topbar .follow{display:flex;align-items:center;gap:8px}
.dot{width:12px;height:12px;border-radius:50%;background:var(--blue);display:inline-block}
.topbar .contact{display:flex;gap:22px;align-items:center}
.topbar .contact span{display:flex;align-items:center;gap:6px}

.header{height:122px;display:flex;align-items:center;justify-content:space-between;padding:0 70px}
.brand{display:flex;align-items:center;gap:14px}
.brand-mark{width:70px;height:70px;border-radius:50%;background:var(--blue)}
.brand-name{font-family:"Roboto Slab",Georgia,serif;font-weight:700;font-size:30px;color:var(--blue);line-height:1.05}
.nav{display:flex;align-items:center;gap:10px;font-size:13px;font-weight:700;letter-spacing:.5px;color:var(--navy)}
.nav a{padding:10px 18px;border-radius:22px}
.nav a.active{background:var(--blue);color:var(--white)}
.nav svg{margin-left:10px}

.hero{height:500px;position:relative;background:linear-gradient(180deg,#8fc3ea 0%,#5e9ccc 35%,#3f6f94 55%,#1f4f78 75%,#2a6a96 100%);display:flex;flex-direction:column;align-items:center;justify-content:center;text-align:center;color:var(--white)}
.hero h1{font-family:"Cinzel",Georgia,serif;font-weight:700;font-size:66px;letter-spacing:3px;margin-top:20px;text-shadow:0 2px 6px rgba(0,0,0,.3)}
.hero p{width:640px;font-size:14px;line-height:1.6;margin-top:10px}
.btn{display:inline-block;background:var(--blue);color:var(--white);font-weight:700;font-size:13px;letter-spacing:.5px;padding:12px 26px;border-radius:24px;text-transform:uppercase}
.hero .btn{margin-top:26px}

.welcome{height:528px;text-align:center;padding-top:56px}
.section-title{font-family:"Cinzel",Georgia,serif;font-size:40px;color:var(--blue);font-weight:400}
.welcome .section-title{font-size:38px}
.rule{width:70px;height:2px;background:var(--blue);margin:12px auto 28px}
.welcome p{width:980px;margin:0 auto 14px;font-size:13px;line-height:1.75;color:var(--muted)}
.welcome .btn{margin-top:26px;padding:14px 34px}

.whatwedo{height:480px;background:linear-gradient(180deg,#1d95df 0%,#0d7fcf 50%,#0a6db6 100%);text-align:center;padding-top:26px}
.whatwedo .section-title,.about .section-title{color:var(--white)}
.whatwedo .rule,.about .rule{background:var(--white)}
.whatwedo .rule{margin-bottom:0}
.cards{display:flex;justify-content:center;gap:36px;margin-top:28px}
.card{background:var(--white);width:320px;height:318px;box-shadow:0 4px 14px rgba(0,0,0,.2)}
.card .photo{height:140px}
.card h3{font-family:"Roboto Slab",Georgia,serif;font-size:21px;color:var(--blue);margin:18px 0 10px}
.card p{font-size:12.5px;line-height:1.7;color:var(--muted);padding:0 24px}
.ph-sunset{background:linear-gradient(180deg,#f2b98a 0%,#c98b7a 40%,#5b6f8c 70%,#2f4a66 100%)}
.ph-harbour{background:linear-gradient(180deg,#9ccbf0 0%,#6ea8d4 45%,#3c6f98 75%,#2a557a 100%)}
.ph-boats{background:linear-gradient(180deg,#d9e3ec 0%,#8fb1cc 45%,#3b6b92 100%)}
.ph-night{background:linear-gradient(180deg,#2b3c66 0%,#c2763c 55%,#3a3148 100%)}
.ph-town{background:linear-gradient(180deg,#b6d3ee 0%,#c9a77f 50%,#5a7891 100%)}

.projects{height:700px;text-align:center;padding-top:56px}
.project-grid{display:flex;justify-content:center;gap:30px;margin-top:10px;text-align:left}
.project{width:510px}
.project .photo{height:250px}
.project h3{font-family:"Roboto Slab",Georgia,serif;font-size:18px;color:var(--navy);margin:22px 0 8px;letter-spacing:.3px}
.project p{font-size:12.5px;line-height:1.7;color:var(--muted)}
.more{display:inline-block;margin-top:8px;font-size:12px;font-weight:700;color:var(--blue)}

.about{height:400px;background:linear-gradient(90deg,#0a6db6 0%,#1793df 60%,#2aa2ea 100%);color:var(--white);display:flex;padding:40px 70px 0 150px;gap:80px}
.about-text{width:580px}
.about .section-title{text-align:left}
.about .rule{margin:12px 0 18px}
.about p{font-size:13px;line-height:1.65;margin-bottom:10px}
.about .btn{background:var(--white);color:var(--blue);margin-top:8px}
.about-badge{display:flex;flex-direction:column;align-items:center;justify-content:center;gap:16px;margin-top:10px}
.about-badge .circle{width:150px;height:150px;border-radius:50%;background:var(--white)}
.about-badge span{font-family:"Roboto Slab",Georgia,serif;font-weight:700;font-size:22px;color:var(--white)}

.news{height:560px;text-align:center;padding-top:56px}
.news-grid{display:flex;justify-content:center;gap:30px;text-align:left}
.news-item{width:330px}
.news-item .photo{height:152px}
.news-item h3{font-family:"Roboto Slab",Georgia,serif;font-size:15px;color:var(--navy);margin:18px 0 4px}
.news-item .date{font-size:11px;color:var(--blue);margin-bottom:6px}
.news-item p{font-size:12.5px;line-height:1.6;color:var(--muted)}

.footer{height:244px;background:var(--blue-deep);color:var(--white);padding:26px 70px 0}
.footer-nav{display:flex;align-items:center;justify-content:space-between;padding-bottom:20px;border-bottom:1px solid rgba(255,255,255,.3)}
.footer-nav .links{display:flex;gap:10px;font-size:12px}
.footer-nav .links a{padding:8px 16px}
.footer-nav .links a.active{border:1px solid var(--white)}
.footer-nav .social{display:flex;gap:10px}
.footer-nav .social .dot{background:var(--white)}
.footer h4{font-family:"Cinzel",Georgia,serif;font-size:18px;font-weight:400;margin:22px 0 16px}
.footer-contact{display:flex;align-items:center;gap:60px;font-size:12px}
.footer-contact .item{display:flex;align-items:center;gap:10px}
.icon{width:30px;height:30px;border-radius:50%;background:var(--white);display:flex;align-items:center;justify-content:center;flex:none}
.footer-contact .copy{margin-left:auto;text-align:right;font-size:11px;line-height:1.5}
.footer-contact .copy strong{font-family:"Roboto Slab",Georgia,serif}
</style>
</head>
<body>

<div class="topbar">
  <div class="follow">Follow Us On <span class="dot"></span><span class="dot"></span><span class="dot"></span></div>
  <div class="contact">
    <span><svg width="12" height="12" viewBox="0 0 24 24"><path fill="#0f86d8" d="M6.6 10.8a15.1 15.1 0 0 0 6.6 6.6l2.2-2.2c.3-.3.7-.4 1-.2 1.1.4 2.3.6 3.6.6.6 0 1 .4 1 1V20c0 .6-.4 1-1 1A17 17 0 0 1 3 4c0-.6.4-1 1-1h3.5c.6 0 1 .4 1 1 0 1.3.2 2.5.6 3.6.1.3 0 .7-.2 1z"/></svg>01481 555 019</span>
    <span><svg width="13" height="11" viewBox="0 0 24 18"><rect x="1" y="1" width="22" height="16" rx="2" fill="none" stroke="#0f86d8" stroke-width="2"/><path d="M1 2l11 8 11-8" fill="none" stroke="#0f86d8" stroke-width="2"/></svg>info@BrenlowEstates.example</span>
  </div>
</div>

<header class="header">
  <div class="brand">
    <div class="brand-mark"></div>
    <div class="brand-name">Brenlow Estates Ltd</div>
  </div>
  <nav class="nav">
    <a class="active" href="#">HOME</a>
    <a href="#">ABOUT</a>
    <a href="#">PROJECTS</a>
    <a href="#">NEWS</a>
    <a href="#">CONTACT</a>
    <svg width="16" height="16" viewBox="0 0 24 24"><circle cx="10" cy="10" r="7" fill="none" stroke="#123a5c" stroke-width="3"/><path d="M15 15l7 7" stroke="#123a5c" stroke-width="3"/></svg>
  </nav>
</header>

<section class="hero" role="img" aria-label="Wide photograph of a Guernsey harbour with moored boats and the town beyond">
  <h1>BRENLOW ESTATES LTD</h1>
  <p>Brenlow Estates Ltd is a family owned Guernsey property holding company, managing homes and commercial premises across the island with care since 1934.</p>
  <a class="btn" href="#">Contact Us</a>
</section>

<section class="welcome">
  <h2 class="section-title">Welcome to Brenlow Estates Ltd</h2>
  <div class="rule"></div>
  <p>Brenlow Estates Limited (BEL) is a family-owned Guernsey property holding company. It purchases properties that are considered to have potential for development, either through refurbishment or by obtaining planning permission to change its classification, for example industrial premises to offices or retail outlets, or by the marriage value of buying adjoining properties.</p>
  <p>An adjoining property to one already owned by BEL, BEL's reputation as a fair-minded landlord stems from the application of the founder's level of working with the tenant to help maximise the business benefits of both parties. There is no capital gains tax on property in the island, which makes buying and letting an attractive enterprise.</p>
  <a class="btn" href="#">Know More</a>
</section>

<section class="whatwedo">
  <h2 class="section-title">What We Do</h2>
  <div class="rule"></div>
  <div class="cards">
    <article class="card">
      <div class="photo ph-sunset" role="img" aria-label="Photograph of a harbour town at sunset"></div>
      <h3>Yesterday</h3>
      <p>BEL was founded in 1934 by Edmund Brenlow to manage both his own extensive investments and his property portfolio.</p>
    </article>
    <article class="card">
      <div class="photo ph-harbour" role="img" aria-label="Photograph of a busy marina under a blue sky"></div>
      <h3>Today</h3>
      <p>The Brenlow family has steadily built on the foundations set out by the founder and each generation develops and grows it.</p>
    </article>
    <article class="card">
      <div class="photo ph-boats" role="img" aria-label="Photograph of small boats moored beside a harbour wall"></div>
      <h3>Tomorrow</h3>
      <p>In keeping with its past proven development philosophy, its intimate understanding of the local property market and the island.</p>
    </article>
  </div>
</section>

<section class="projects">
  <h2 class="section-title">Our Projects</h2>
  <div class="rule"></div>
  <div class="project-grid">
    <article class="project">
      <div class="photo ph-sunset" role="img" aria-label="Photograph of waterfront buildings at dusk"></div>
      <h3>LOREM IPSUM IS SIMPLY DUMMY TEXT OF THE</h3>
      <p>Lorem Ipsum is simply dummy text of the printing and typesetting industry. Lorem Ipsum has been the industry's standard dummy text ever since the 1500s, when an unknown printer took a galley of type.</p>
      <a class="more" href="#">READ MORE »</a>
    </article>
    <article class="project">
      <div class="photo ph-night" role="img" aria-label="Photograph of a harbour town lit up at night"></div>
      <h3>LOREM IPSUM IS SIMPLY DUMMY TEXT OF THE</h3>
      <p>Lorem Ipsum is simply dummy text of the printing and typesetting industry. Lorem Ipsum has been the industry's standard dummy text ever since the 1500s, when an unknown printer took a galley of type.</p>
      <a class="more" href="#">READ MORE »</a>
    </article>
  </div>
</section>

<section class="about">
  <div class="about-text">
    <h2 class="section-title">About Us</h2>
    <div class="rule"></div>
    <p>The Bailiwick of Guernsey is a British Crown dependency in the English Channel. The benefit of establishing a company in Guernsey is the island's low tax jurisdiction since there are no capital taxes and its corporation taxes for many companies. Consequently, since the 1960s the island's development as an international centre for the administration of institutions and trusts has thrived.</p>
    <p>There are currently more than 100 companies registered with the Sarnian Business Registry Board: banks, fund managers, building societies, stock brokerage and asset management firms.</p>
    <a class="btn" href="#">Know More</a>
  </div>
  <div class="about-badge">
    <div class="circle"></div>
    <span>Brenlow Estates</span>
  </div>
</section>

<section class="news">
  <h2 class="section-title">Latest News</h2>
  <div class="rule"></div>
  <div class="news-grid">
    <article class="news-item">
      <div class="photo ph-harbour" role="img" aria-label="Aerial photograph of a marina and town"></div>
      <h3>LOREM IPSUM IS SIMPLE DUMMY TEXT</h3>
      <div class="date">Posted by 27 Dec</div>
      <p>Lorem Ipsum is simply dummy text of the printing and typesetting industry. Lorem Ipsum has been the industry's standard dummy text.</p>
    </article>
    <article class="news-item">
      <div class="photo ph-town" role="img" aria-label="Photograph of harbourside houses and boats"></div>
      <h3>LOREM IPSUM IS SIMPLE DUMMY TEXT</h3>
      <div class="date">Posted by 27 Dec</div>
      <p>Lorem Ipsum is simply dummy text of the printing and typesetting industry. Lorem Ipsum has been the industry's standard dummy text.</p>
    </article>
    <article class="news-item">
      <div class="photo ph-boats" role="img" aria-label="Photograph of boats in a harbour with the town behind"></div>
      <h3>LOREM IPSUM IS SIMPLE DUMMY TEXT</h3>
      <div class="date">Posted by 27 Dec</div>
      <p>Lorem Ipsum is simply dummy text of the printing and typesetting industry. Lorem Ipsum has been the industry's standard dummy text.</p>
    </article>
  </div>
</section>

<footer class="footer">
  <div class="footer-nav">
    <div class="links">
      <a class="active" href="#">Home</a>
      <a href="#">About</a>
      <a href="#">Projects</a>
      <a href="#">News</a>
      <a href="#">Contact Us</a>
    </div>
    <div class="social"><span class="dot"></span><span class="dot"></span><span class="dot"></span></div>
  </div>
  <h4>Contact Us</h4>
  <div class="footer-contact">
    <div class="item">
      <span class="icon"><svg width="14" height="16" viewBox="0 0 24 28"><path fill="#0a6db6" d="M12 0a10 10 0 0 0-10 10c0 7.5 10 18 10 18s10-10.5 10-18A10 10 0 0 0 12 0zm0 14a4 4 0 1 1 0-8 4 4 0 0 1 0 8z"/></svg></span>
      <span>12 Harbour Row, St Peter Port<br>Guernsey GY1 2AB</span>
    </div>
    <div class="item">
      <span class="icon"><svg width="14" height="14" viewBox="0 0 24 24"><path fill="#0a6db6" d="M6.6 10.8a15.1 15.1 0 0 0 6.6 6.6l2.2-2.2c.3-.3.7-.4 1-.2 1.1.4 2.3.6 3.6.6.6 0 1 .4 1 1V20c0 .6-.4 1-1 1A17 17 0 0 1 3 4c0-.6.4-1 1-1h3.5c.6 0 1 .4 1 1 0 1.3.2 2.5.6 3.6.1.3 0 .7-.2 1z"/></svg></span>
      <span>01481 555 019</span>
    </div>
    <div class="item">
      <span class="icon"><svg width="14" height="11" viewBox="0 0 24 18"><rect x="1" y="1" width="22" height="16" rx="2" fill="none" stroke="#0a6db6" stroke-width="2"/><path d="M1 2l11 8 11-8" fill="none" stroke="#0a6db6" stroke-width="2"/></svg></span>
      <span>info@BrenlowEstates.example</span>
    </div>
    <div class="copy">© <strong>Brenlow Estates Ltd</strong> 2016. All<br>Rights Reserved</div>
  </div>
</footer>

</body>
</html>
```